Multipage Package Insert Leaflet

Hi, we currently sell a charging station that comes with a teeny tiny generic instruction manual - we are looking to create a large horizontal 7inch x 6inch - less words, more pictures. Imagine you bought an LUMETAB or any Quince Product- that's kind of the look we're shooting for - mostly colorful images, less words. Please create a graphic rendering of product if you need to. Here are the things that should be in this instruction manual (not in this wording, use your own words)

1. scan image using messenger APP to order additional cables (see project brief - it's the strange looking letter S)
2. the button on the unit is NOT a power button, but it turns the blue light on or off. the unit is on as long as it is plugged in.
3. the plastic dividers should be pushed into the space allotted - use some muscle - push it down until you hear a "snap" - once inserted it can can be removed, put some muscle into it. plastic dividers can be removed to accomodate thicker bulkier phone and tablet cases.
4. one of the baffle will always glow blue when plugged in if the "on" button is on
5. when "blue light is on" the baffle that is charging a device will start to glow
6. unit will stop charging - and blue light will turn off, when a device is fully charged

Troubleshoot:
1. what to do if blue light not working - answer - check to make sure power button is on "on" position. Make sure plastic divider is snapped all the way down (it will make a distinctive "snap" sound. If you have trouble try flipping the plastic divider and try the other direction - sometimes one side fits better than the other
2. you break something and need a part - answer: contact us anytime at INFO@Brantowlgear.com, if we have the spare part (and we usually do) we'll be happy to replace it for you.
3. you need extra USB cables - go to www.Brantowlgear.com/Cable to order more or different cables
4. item stopped working - you have a 1year warranty - please email us INFO@BrantowlGear.com
5. on the "BACK" side of this instruction maual please include some contact us information on there:
email us anytime, we're real people who reads and writes emails!
info@BrantowlGear.com
Mirela@BrantowlGear.com
Oswin@BrantowlGear.com
Connect with us on Facebook at Facebook.com/BrantowlGear

we image this leaflet/instruction manual will be 6-12 pages - mostly images, the less text the better.

Designers can submit just ONE-page to get feedback on what we think of overall theme/design/colors. We are very active on this platform and will always provide feedback very quickly. We look forward to all your submissions.

Font styles to use
Serif

Colors
ffffff

Requirements
Must have
• graphics, images, nice background, product image rendering if needed to illustrate certain things. All images included designers are free to use as they wish, but should have some graphic rendering of their own to illustrate any necessary points as discussed above
Nice to have
• a step by step guide on how to use the item. item comes with powercord, 6x USB cables, 7 plastic dividers that fits in the 7 slots on unit. graphic renderings to illustrate how-to would be super.
Should not have
• spelling errors or grammar errors of any sort

```html
<!DOCTYPE html>
<html lang="en">
<head>
<meta charset="utf-8">
<title>Troubleshooting – Page 7</title>
<link href="https://fonts.googleapis.com/css2?family=Roboto:wght@300;400;700&display=swap" rel="stylesheet">
<style>
  :root {
    --brand-blue: #0080cc;
    --ink: #1a1a1a;
    --paper: #ffffff;
    --sand: #e9e2d6;
    --sand-line: #d9d9d9;
    --rule: #1a1a1a;
  }
  html, body {
    margin: 0;
    padding: 0;
    width: 1029px;
    height: 1200px;
    overflow: hidden;
    background: var(--paper);
  }
  .page {
    position: relative;
    width: 1029px;
    height: 1200px;
    overflow: hidden;
    font-family: "Roboto", Arial, sans-serif;
    color: var(--ink);
  }
  .page-decor {
    position: absolute;
    inset: 0;
  }
  .title-band {
    position: absolute;
    left: 67px;
    top: 46px;
    width: 915px;
    height: 178px;
    background: var(--brand-blue);
    overflow: hidden;
  }
  .title-band h1 {
    position: absolute;
    left: 44px;
    bottom: -11px;
    margin: 0;
    font-weight: 300;
    font-size: 61px;
    letter-spacing: -0.5px;
    color: var(--paper);
    line-height: 1;
  }
  .question {
    position: absolute;
    left: 102px;
    top: 280px;
    margin: 0;
    font-size: 27px;
    font-weight: 700;
  }
  .question .accent { color: var(--brand-blue); }
  .step {
    position: absolute;
    left: 102px;
    margin: 0;
    font-size: 20.5px;
    font-weight: 300;
    line-height: 26px;
  }
  .step-num {
    position: absolute;
    left: 0;
    font-weight: 700;
  }
  .step-text { display: block; padding-left: 33px; }
  .step strong { font-weight: 700; }
  .step-one { top: 326px; }
  .step-two { top: 962px; }
  .product-photo {
    position: absolute;
    left: 200px;
    top: 392px;
    width: 656px;
    height: 520px;
    border-radius: 14px;
    background: linear-gradient(160deg, #2a2a2e 0%, #4a4d55 38%, #c9cbcf 62%, #e6e7e9 100%);
  }
  .callouts {
    position: absolute;
    inset: 0;
  }
  .page-number {
    position: absolute;
    left: 932px;
    top: 1108px;
    margin: 0;
    font-size: 30px;
    font-weight: 700;
  }
  .page-number .digit {
    font-weight: 300;
    font-size: 48px;
  }
</style>
</head>
<body>
<div class="page">
  <svg class="page-decor" width="1029" height="1200" viewBox="0 0 1029 1200" aria-hidden="true">
    <polygon points="1029,800 1029,1200 680,1200 680,1080 808,1080 1029,860" fill="var(--sand)"/>
    <polygon points="972,792 1029,748 1029,782 972,826" fill="var(--sand)"/>
    <polygon points="530,1200 640,1116 656,1116 546,1200" fill="var(--sand-line)"/>
    <polygon points="700,1200 808,1116 824,1116 716,1200" fill="var(--paper)"/>
  </svg>

  <header class="title-band">
    <h1>TROUBLESHOOTING</h1>
  </header>

  <h2 class="question">What to do if <span class="accent">“BLUE LIGHT”</span> is not working?</h2>

  <p class="step step-one">
    <span class="step-num">1.</span>
    <span class="step-text">Check if the power button is<br>properly turned <strong>“ON”</strong>.</span>
  </p>

  <div class="product-photo" role="img" aria-label="Photo of the silver charging station with a phone docked behind a glowing blue plastic divider, power button on the front"></div>

  <svg class="callouts" width="1029" height="1200" viewBox="0 0 1029 1200" aria-hidden="true">
    <defs>
      <marker id="arrowhead" markerWidth="10" markerHeight="8" refX="9" refY="4" orient="auto">
        <path d="M0,0 L10,4 L0,8 Z" fill="var(--rule)"/>
      </marker>
    </defs>
    <polyline points="164,396 164,692 278,737" fill="none" stroke="var(--rule)" stroke-width="1.6" marker-end="url(#arrowhead)"/>
    <polyline points="562,1016 616,1016 918,666 774,630" fill="none" stroke="var(--rule)" stroke-width="1.6" marker-end="url(#arrowhead)"/>
  </svg>

  <p class="step step-two">
    <span class="step-num">2.</span>
    <span class="step-text">Make sure plastic divider is snapped all the<br>way down (it will make a distinctive <strong>“SNAP”</strong><br>sound. If you have trouble, try flipping the<br>plastic divider the other direction - sometimes<br>one side fits better than the other.</span>
  </p>

  <p class="page-number">p<span class="digit">7</span></p>
</div>
</body>
</html>
```